Wordpress website for Dance Studio

Hi there, I am looking for Wordpress Website for dance studio. Happy for designed to use available themes. Would like a few pages setup and I can do the rest.

Other things I would like included in this theme :

Nice images page OR moving banner
Blog
Ability for youtubes

Other than that, simple requirements, just a gorgeous looking landing page/site etc.

Target Market(s)

Dance mums and kids (dancers)

Industry/Entity Type

Dance and Performancer

Coding

Coded - Design and coding required

Number of Pages Required

4 page

Font styles to use
Sans Serif

Colors
EB3D1F
EC4F4E
F09395
F8D3D4
FCEDEE

Requirements
Must have
• Wordpress theme
Nice to have
• Artistic, graphical, dance studio theme

```html
<!DOCTYPE html>
<html lang="en">
<head>
<meta charset="utf-8">
<title>Pirouette Lane — Dance Studio</title>
<link rel="stylesheet" href="https://fonts.googleapis.com/css2?family=Jost:ital,wght@0,400;0,500;0,600;1,400&family=Arimo:ital,wght@0,400;1,400&display=swap">
<style>
:root{
  --red:#e8291e;
  --red-soft:#ec4f4e;
  --band:#e8434b;
  --pink:#f09395;
  --blush:#f8d3d4;
  --ink:#1e1e1e;
  --text:#444;
  --muted:#666;
  --dark:#1c1c1c;
  --white:#fff;
}
*{box-sizing:border-box;margin:0;padding:0}
html,body{width:1200px;height:3354px;overflow:hidden;background:var(--white)}
body{position:relative;font-family:"Arimo",Arial,sans-serif;color:var(--text)}
.abs{position:absolute}
.topline{left:0;top:0;width:1200px;height:3px;background:var(--red)}
.brand{font-family:"Jost",sans-serif;font-weight:600;color:var(--red);font-size:32px;letter-spacing:.5px}
.site-logo{left:111px;top:44px}
.nav{top:55px;display:flex;gap:0;font-family:"Jost",sans-serif;font-size:17px;color:var(--ink)}
.nav a{color:inherit;text-decoration:none;position:absolute;white-space:nowrap}
.nav a.active{color:var(--red)}
.hero{left:0;top:136px;width:1200px;height:762px;background:linear-gradient(160deg,#cdbba8 0%,#e9e4dc 45%,#b48a66 100%)}
.hero-title{left:380px;top:602px;width:440px;height:64px;background:rgba(232,41,30,.85);color:#fff;font-family:"Jost",sans-serif;font-weight:600;font-size:36px;letter-spacing:1px;display:flex;align-items:center;justify-content:center}
.hero-sub{left:215px;top:672px;width:770px;height:64px;background:rgba(40,40,40,.75);color:#fff;font-family:"Jost",sans-serif;font-size:25px;display:flex;align-items:center;justify-content:center;letter-spacing:.5px}
.dots{left:576px;top:872px;display:flex;gap:9px}
.dots span{width:11px;height:11px;border-radius:50%;background:#111}
.dots span.on{background:var(--red)}
.welcome-pre{left:0;width:1200px;top:955px;text-align:center;font-family:"Jost",sans-serif;font-size:29px;color:var(--ink)}
.welcome-title{left:0;width:1200px;top:982px;text-align:center;font-size:46px}
.intro{left:232px;width:736px;top:1068px;text-align:center;font-size:14.5px;line-height:31px;color:var(--text)}
.btn{left:502px;top:1215px;width:198px;height:55px;border-radius:28px;background:var(--red);color:#fff;font-family:"Jost",sans-serif;font-weight:500;font-size:18px;display:flex;align-items:center;justify-content:center}
.band{left:0;top:1557px;width:1200px;height:630px;background:var(--band)}
.video{left:200px;top:1333px;width:800px;height:441px;border:4px solid #fff;background:linear-gradient(135deg,#6e5a5e,#8a7478 55%,#5b4a49)}
.play{left:550px;top:1503px}
.avatar{left:540px;top:1840px;width:120px;height:120px;border-radius:50%;background:linear-gradient(135deg,#7a4f3d,#c9977d);border:2px solid #fff}
.arrow{top:1973px;width:42px;height:41px;border:2px solid #fff;display:flex;align-items:center;justify-content:center}
.quote{left:250px;width:700px;top:1975px;text-align:center;color:#fff;font-style:italic;font-size:14px;line-height:27.5px}
.qmark{font-family:"Jost",sans-serif;font-size:34px;font-style:normal;line-height:0;vertical-align:-10px}
.who{left:0;width:1200px;top:2103px;text-align:center;color:#fff;font-family:"Jost",sans-serif;font-weight:500;font-size:18px}
.stars{left:0;width:1200px;top:2128px;text-align:center;color:#fff;font-size:13px;letter-spacing:2px}
.blog-title{left:0;width:1200px;top:2236px;text-align:center;font-family:"Jost",sans-serif;font-weight:500;font-size:41px;color:var(--ink)}
.rule{left:577px;top:2298px;width:46px;height:3px;background:var(--red)}
.post-img{top:2334px;width:313px;height:276px}
.card{top:2555px;width:287px;height:220px;background:#fff;box-shadow:0 2px 8px rgba(0,0,0,.12);text-align:center;padding-top:21px}
.card .date{color:var(--red);font-family:"Jost",sans-serif;font-size:20px}
.card h3{font-family:"Jost",sans-serif;font-weight:400;font-size:18px;line-height:27px;color:var(--ink);margin-top:10px}
.card p{font-size:13px;line-height:24px;color:var(--muted);margin-top:9px;padding:0 14px}
.footer{left:0;top:2876px;width:1200px;height:478px;background:var(--dark);color:#fff}
.fnav{top:52px;font-family:"Jost",sans-serif;font-size:17px}
.fnav span{position:absolute;white-space:nowrap}
.fline{left:111px;width:978px;height:1px;background:#333}
.fhead{top:132px;font-family:"Jost",sans-serif;font-weight:500;font-size:21px;letter-spacing:.5px}
.field{background:#fff;color:#333;font-size:11px;padding:11px 12px}
.submit{left:111px;top:342px;width:97px;height:32px;background:var(--red);color:#fff;font-size:13px;display:flex;align-items:center;justify-content:center}
.ci{left:555px;width:42px;height:42px;border-radius:50%;border:2px solid #fff;display:flex;align-items:center;justify-content:center}
.ct{left:612px;font-family:"Jost",sans-serif;font-size:14px;line-height:21px}
.ct small{font-size:13px;display:block}
.flogo{left:824px;top:200px;font-size:29px;color:#fff}
.social{top:270px;width:35px;height:35px;border-radius:50%;border:2px solid #fff}
.copy{left:0;width:1200px;top:436px;text-align:center;font-family:"Jost",sans-serif;font-size:15px}
</style>
</head>
<body>
<div class="abs topline"></div>
<header>
  <div class="abs brand site-logo">Pirouette Lane</div>
  <nav class="abs nav" style="left:0">
    <a class="active" style="left:632px">Home</a>
    <a style="left:722px">About Us</a>
    <a style="left:837px">Blog</a>
    <a style="left:916px">Video</a>
    <a style="left:1007px">Contact Us</a>
  </nav>
</header>

<section>
  <div class="abs hero" role="img" aria-label="Photo of a mother and daughter practising ballet arabesques in a bright studio"></div>
  <div class="abs hero-title">PIROUETTE LANE</div>
  <div class="abs hero-sub">Sed ut perspiciatis unde omnis iste natus error sit voluptatem</div>
  <div class="abs dots"><span></span><span class="on"></span><span></span></div>
</section>

<section>
  <div class="abs welcome-pre">WELCOME TO</div>
  <div class="abs brand welcome-title">Pirouette Lane</div>
  <p class="abs intro">Sed ut perspiciatis unde omnis iste natus error sit voluptatem accusantium doloremque laudantium, totam rem aperiam, eaque ipsa quae ab illo inventore veritatis et quasi architecto beatae vitae dicta sunt explicabo. Nemo enim ipsam voluptatem quia voluptas sit aspernatur aut odit aut fugit, sed quia consequuntur magni dolores eos accusantium doloremque qui ratione voluptatem sequi nesciunt.</p>
  <div class="abs btn">LEARN MORE</div>
</section>

<section>
  <div class="abs band" role="img" aria-label="Faint photo of a dancer under a red overlay"></div>
  <div class="abs video" role="img" aria-label="Video still of a mother and daughter dancing together"></div>
  <svg class="abs play" width="100" height="100" viewBox="0 0 100 100"><circle cx="50" cy="50" r="47" fill="rgba(0,0,0,.15)" stroke="#fff" stroke-width="3"/><path d="M40 33 L68 50 L40 67 Z" fill="#fff"/></svg>

  <div class="abs avatar" role="img" aria-label="Portrait of a smiling parent"></div>
  <div class="abs arrow" style="left:172px"><svg width="10" height="10" viewBox="0 0 10 10"><path d="M7 1 L3 5 L7 9" fill="none" stroke="#fff" stroke-width="1.5"/></svg></div>
  <div class="abs arrow" style="left:985px"><svg width="10" height="10" viewBox="0 0 10 10"><path d="M3 1 L7 5 L3 9" fill="none" stroke="#fff" stroke-width="1.5"/></svg></div>
  <p class="abs quote"><span class="qmark">&ldquo;</span> Sed ut perspiciatis unde omnis iste natus error sit voluptatem accusantium doloremque laudantium, totam rem aperiam, eaque ipsa quae illo inventore veritatis et quasi architecto beatae vitae dicta sunt explicabo. Nemo enim ipsam voluptatem quia voluptas sit aspernatur aut odit aut fugit, sed quia consequuntur magni dolores eos qui ratione voluptatem sequi nesciunt. <span class="qmark">&rdquo;</span></p>
  <div class="abs who">JHON SMITH</div>
  <div class="abs stars">★★★★★</div>
</section>

<section>
  <h2 class="abs blog-title">Latest Blog</h2>
  <div class="abs rule"></div>

  <div class="abs post-img" style="left:111px;background:linear-gradient(150deg,#b99c85,#e4ddd4 60%,#a88566)" role="img" aria-label="Photo of dancers in a studio"></div>
  <div class="abs post-img" style="left:444px;background:linear-gradient(150deg,#5c4a40,#8d7a70 55%,#3c3431)" role="img" aria-label="Photo of a ballet teacher with young pupils"></div>
  <div class="abs post-img" style="left:776px;background:linear-gradient(150deg,#d9c7b5,#f3eee7 55%,#e6cfa8)" role="img" aria-label="Photo of young ballerinas stretching"></div>

  <article class="abs card" style="left:127px"><div class="date">08 NOV 2021</div><h3>Sed ut perspiciatis unde<br>omnis iste natus</h3><p>Nemo enim ipsam voluptatem quia voluptas sit aspernatur aut odit aut fugit, eos qui ratione voluptatem</p></article>
  <article class="abs card" style="left:460px"><div class="date">08 NOV 2021</div><h3>Sed ut perspiciatis unde<br>omnis iste natus</h3><p>Nemo enim ipsam voluptatem quia voluptas sit aspernatur aut odit aut fugit, eos qui ratione voluptatem</p></article>
  <article class="abs card" style="left:792px"><div class="date">08 NOV 2021</div><h3>Sed ut perspiciatis unde<br>omnis iste natus</h3><p>Nemo enim ipsam voluptatem quia voluptas sit aspernatur aut odit aut fugit, eos qui ratione voluptatem</p></article>
</section>

<footer class="abs footer">
  <nav class="abs fnav" style="left:0">
    <span style="left:371px">Home</span><span style="left:461px">About Us</span><span style="left:576px">Blog</span><span style="left:655px">Video</span><span style="left:746px">Contact Us</span>
  </nav>
  <div class="abs fline" style="top:100px"></div>

  <div class="abs fhead" style="left:113px">CONTACT US</div>
  <div class="abs field" style="left:113px;top:190px;width:181px;height:35px">First Name :</div>
  <div class="abs field" style="left:303px;top:190px;width:181px;height:35px">Last Name :</div>
  <div class="abs field" style="left:113px;top:234px;width:181px;height:35px">Email :</div>
  <div class="abs field" style="left:303px;top:234px;width:181px;height:35px">Phone :</div>
  <div class="abs field" style="left:113px;top:278px;width:371px;height:54px">Message :</div>
  <div class="abs submit">SUBMIT</div>

  <div class="abs fhead" style="left:562px">ADDRESS</div>
  <div class="abs ci" style="top:191px"><svg width="16" height="18" viewBox="0 0 16 18"><path d="M8 1a5.5 5.5 0 0 0-5.5 5.5C2.5 11 8 17 8 17s5.5-6 5.5-10.5A5.5 5.5 0 0 0 8 1z" fill="none" stroke="#fff" stroke-width="1.6"/><circle cx="8" cy="6.5" r="2" fill="#fff"/></svg></div>
  <div class="abs ct" style="top:189px">ADDRESS<small># 125 Lorem Ipsum Dummy</small></div>
  <div class="abs ci" style="top:252px"><svg width="16" height="16" viewBox="0 0 16 16"><path d="M3 1.5l3 .5 1 3.5-2 1.5c1 2 2 3 4 4l1.5-2 3.5 1 .5 3c-6 1-12-5-11.5-11.5z" fill="none" stroke="#fff" stroke-width="1.4"/></svg></div>
  <div class="abs ct" style="top:251px">PHONE<small>000.121.1231</small></div>
  <div class="abs ci" style="top:316px"><svg width="16" height="12" viewBox="0 0 16 12"><rect x="1" y="1" width="14" height="10" fill="#fff"/><path d="M1 1l7 5 7-5" fill="none" stroke="#1c1c1c" stroke-width="1.4"/></svg></div>
  <div class="abs ct" style="top:316px">EMAIL US<small>info@compnayname.com</small></div>

  <div class="abs brand flogo">Pirouette Lane</div>
  <div class="abs social" style="left:852px"></div>
  <div class="abs social" style="left:895px"></div>
  <div class="abs social" style="left:938px"></div>
  <div class="abs social" style="left:981px"></div>
  <div class="abs social" style="left:1024px"></div>

  <div class="abs fline" style="top:404px"></div>
  <div class="abs copy">© Copyright 2021 Pirouette Lane.All Rights Reserved</div>
</footer>
</body>
</html>
```